CBD AgriBusiness Verdant Trophy Business Card

We are HiTec producer of medical cannabis CBD Switzerland of high quality. Our website is alpinleaf.net, we will also revisit it graphically, the winner of this contest will be the graphic designer chosen for the new design of the website. We stand out by the skill of the team, many of our engineers we win cup cannabis. I join the current map to take as an example but to revisit completely: deletion of surname and first name, modification of funds (front / back), reorganization of text info, highlighting the address of the website. three characteristics define the business card: Professional, Class, refined. The business card must be optimized for soft-touch and selective varnish printing.

Target Market(s)

Customers and Suppliers

Industry/Entity Type

Agribusiness

Contact Information for Business Card

Logo, Tél / Whatsapp, mail, url du site : alpinleaf.net

Font styles to use
Sans Serif

Requirements
Must have
• Logo of alpinleaf.net
Nice to have
• a design that stands out well on the selective varnish
Should not have
• Last name and first name

```html
<!DOCTYPE html>
<html lang="en">
<head>
<meta charset="utf-8">
<title>Alpinleaf Business Card</title>
<link rel="stylesheet" href="https://fonts.googleapis.com/css2?family=Montserrat:wght@300;400;700;800&display=swap">
<style>
  :root {
    --page: #4a4c50;
    --card: #0b0b0b;
    --white: #ffffff;
    --green: #7fcc4e;
    --leaf-dark: #1f2a14;
    --leaf-mid: #4d6328;
    --leaf-light: #6f8a3a;
    --muted: #d8d8d8;
  }
  * { margin: 0; padding: 0; box-sizing: border-box; }
  html, body { width: 1200px; height: 960px; overflow: hidden; }
  body {
    background: var(--page);
    font-family: "Montserrat", sans-serif;
    display: flex;
    flex-direction: column;
    align-items: center;
    justify-content: center;
    gap: 40px;
  }
  .card {
    position: relative;
    width: 700px;
    height: 400px;
    background: var(--card);
    overflow: hidden;
    box-shadow: 0 10px 28px rgba(0,0,0,0.35);
  }
  .foliage {
    position: absolute;
    border-radius: 50%;
    filter: blur(6px);
  }
  .card-front .foliage-left {
    left: -120px; top: -40px; width: 340px; height: 480px;
    background: radial-gradient(ellipse at 40% 50%, var(--leaf-light) 0%, var(--leaf-mid) 35%, var(--leaf-dark) 60%, transparent 75%);
  }
  .card-front .foliage-right {
    right: -110px; top: 90px; width: 320px; height: 300px;
    background: radial-gradient(ellipse at 45% 50%, var(--leaf-light) 0%, var(--leaf-mid) 35%, var(--leaf-dark) 60%, transparent 75%);
  }
  .card-back .foliage-right {
    right: -130px; top: -80px; width: 430px; height: 520px;
    background: radial-gradient(ellipse at 45% 45%, var(--leaf-light) 0%, var(--leaf-mid) 35%, var(--leaf-dark) 60%, transparent 76%);
  }
  .brand {
    position: absolute;
    display: flex;
    align-items: center;
    gap: 14px;
  }
  .brand-mark {
    width: 34px; height: 34px;
    background: var(--green);
  }
  .brand-name {
    color: var(--white);
    font-weight: 800;
    font-size: 64px;
    letter-spacing: -1px;
    line-height: 1;
  }
  .card-front .brand { left: 170px; top: 150px; }
  .tagline {
    position: absolute;
    left: 218px; top: 232px;
    color: var(--muted);
    font-weight: 400;
    font-size: 15px;
    letter-spacing: 4px;
  }
  .card-back .brand { left: 50px; top: 80px; }
  .card-back .brand-name { font-size: 58px; }
  .contacts {
    position: absolute;
    left: 98px; top: 178px;
    list-style: none;
    display: flex;
    flex-direction: column;
    gap: 14px;
  }
  .contact {
    display: flex;
    align-items: center;
    gap: 12px;
    color: var(--white);
    font-size: 17px;
    font-weight: 300;
    line-height: 24px;
  }
  .contact svg { width: 24px; height: 24px; flex: none; }
  .contact-web {
    margin-top: 6px;
    color: var(--green);
    font-size: 22px;
    font-weight: 700;
  }
  .contact-web svg { width: 28px; height: 28px; }
</style>
</head>
<body>
  <section class="card card-front" aria-label="Card front">
    <div class="foliage foliage-left" role="img" aria-label="Photograph of green cannabis leaves"></div>
    <div class="foliage foliage-right" role="img" aria-label="Photograph of green cannabis leaves"></div>
    <div class="brand">
      <span class="brand-mark"></span>
      <span class="brand-name">alpinleaf</span>
    </div>
    <p class="tagline">ALPIN LEAF UNITED</p>
  </section>

  <section class="card card-back" aria-label="Card back">
    <div class="foliage foliage-right" role="img" aria-label="Photograph of green cannabis plant"></div>
    <div class="brand">
      <span class="brand-mark"></span>
      <span class="brand-name">alpinleaf</span>
    </div>
    <ul class="contacts">
      <li class="contact contact-chat">
        <svg viewBox="0 0 24 24" fill="none" stroke="var(--green)" stroke-width="1.6"><circle cx="12" cy="12" r="10.5"/><path d="M7 8h10v6h-6l-3 3v-3H7z" fill="var(--green)" stroke="none"/></svg>
        123-555-0190
      </li>
      <li class="contact contact-phone">
        <svg viewBox="0 0 24 24" fill="none" stroke="var(--green)" stroke-width="1.6"><circle cx="12" cy="12" r="10.5"/><path d="M8.5 7l2 2.2-1.2 1.6c.8 1.6 2 2.8 3.6 3.6l1.6-1.2 2.2 2-1.3 1.6C11.5 16.4 7.6 12.5 7 8.3z" fill="var(--green)" stroke="none"/></svg>
        123-555-0190
      </li>
      <li class="contact contact-mail">
        <svg viewBox="0 0 24 24" fill="none" stroke="var(--green)" stroke-width="1.6"><circle cx="12" cy="12" r="10.5"/><rect x="6.5" y="8" width="11" height="8" fill="var(--green)" stroke="none"/><path d="M6.5 8l5.5 4.5L17.5 8" stroke="var(--card)" stroke-width="1.2"/></svg>
        hello@alpinleaf.net
      </li>
      <li class="contact contact-web">
        <svg viewBox="0 0 24 24" fill="none" stroke="var(--green)" stroke-width="1.6"><circle cx="12" cy="12" r="10.5"/><circle cx="12" cy="12" r="5.5"/><path d="M6.5 12h11M12 6.5c2 2 2 9 0 11M12 6.5c-2 2-2 9 0 11" stroke-width="1.1"/></svg>
        www.alpinleaf.net
      </li>
    </ul>
  </section>
</body>
</html>
```